Business Card Design

New business card design

Target Market(s)

Residential & Commercial Property Managers

Industry/Entity Type

Plumbing Services

Contact Information for Business Card

Name - Rowan Keddle, title - Director, Phone Number - 0431 286 517, email - rowan@tbk-plumbing.com.au, Company ABN - 73 215 904 386,

Font styles to use
Sans Serif

Colors
0054AA
0677BA
7BADD7
CADEEF
E8F1F8

```html
<!DOCTYPE html>
<html lang="en">
<head>
<meta charset="utf-8">
<title>TBK Plumbing Services – Business Card</title>
<link rel="stylesheet" href="https://fonts.googleapis.com/css2?family=Questrial&family=Roboto:wght@300;400&display=swap">
<style>
  :root {
    --page-bg: #c9c9cb;
    --card-white: #ffffff;
    --card-dark: #1e232a;
    --card-blue: #0a8cc6;
    --brand-blue: #0677ba;
    --accent-blue: #17a3e6;
    --ink: #1e232a;
    --ink-soft: #3a3f46;
    --tint: #e8f1f8;
  }
  * { margin: 0; padding: 0; box-sizing: border-box; }
  html, body { width: 1200px; height: 900px; overflow: hidden; }
  body {
    background: var(--page-bg);
    font-family: "Roboto", Arial, sans-serif;
    display: flex;
    flex-direction: column;
    align-items: center;
    justify-content: center;
    gap: 40px;
  }
  .card {
    position: relative;
    width: 700px;
    height: 400px;
    border-radius: 34px;
    overflow: hidden;
    box-shadow: 0 10px 24px rgba(0, 0, 0, 0.25);
  }

  /* Large faint decoration area, right side */
  .watermark {
    position: absolute;
    right: 40px;
    top: 30px;
    width: 300px;
    height: 330px;
    border-radius: 50%;
  }
  .card--front .watermark {
    background: radial-gradient(circle, rgba(30, 35, 42, 0.28) 0%, rgba(30, 35, 42, 0) 70%);
  }
  .card--back .watermark {
    background: radial-gradient(circle, rgba(202, 222, 239, 0.55) 0%, rgba(232, 241, 248, 0) 70%);
  }

  .company-name {
    position: relative;
    font-family: "Questrial", Arial, sans-serif;
    font-weight: 400;
    white-space: nowrap;
  }

  /* Front */
  .card--front {
    background: linear-gradient(28deg, var(--card-dark) 0%, var(--card-dark) 42%, #12506f 72%, var(--card-blue) 100%);
    display: flex;
    align-items: center;
    justify-content: center;
  }
  .card--front .company-name {
    font-size: 50px;
    color: #ffffff;
  }

  /* Back */
  .card--back { background: var(--card-white); }
  .card--back .company-name {
    position: absolute;
    left: 56px;
    top: 70px;
    font-size: 44px;
    color: var(--ink);
  }

  .contact {
    position: absolute;
    left: 60px;
    bottom: 44px;
  }
  .contact__name {
    font-family: "Questrial", Arial, sans-serif;
    font-size: 38px;
    color: var(--ink);
    line-height: 1.05;
  }
  .contact__title {
    font-size: 24px;
    color: var(--accent-blue);
    margin-bottom: 14px;
  }
  .contact__line {
    display: flex;
    align-items: center;
    gap: 12px;
    font-size: 21px;
    font-weight: 300;
    color: var(--ink-soft);
    line-height: 1.35;
  }
  .contact__icon { width: 20px; height: 20px; flex: none; }
  .abn {
    position: absolute;
    right: 40px;
    bottom: 150px;
    font-size: 20px;
    color: var(--ink-soft);
  }
  .abn__label { color: var(--accent-blue); }
</style>
</head>
<body>
  <section class="card card--front" aria-label="Card front">
    <div class="watermark" role="img" aria-label="Large faint brand decoration"></div>
    <p class="company-name">tbk plumbing services</p>
  </section>

  <section class="card card--back" aria-label="Card back">
    <div class="watermark" role="img" aria-label="Large faint brand decoration"></div>
    <p class="company-name">tbk plumbing services</p>

    <div class="contact">
      <p class="contact__name">Rowan Keddle</p>
      <p class="contact__title">Director</p>
      <p class="contact__line">
        <svg class="contact__icon" viewBox="0 0 24 24" aria-hidden="true">
          <path fill="#17a3e6" d="M6.6 10.8a15.1 15.1 0 0 0 6.6 6.6l2.2-2.2a1 1 0 0 1 1-.25 11.4 11.4 0 0 0 3.6.57 1 1 0 0 1 1 1V20a1 1 0 0 1-1 1A17 17 0 0 1 3 4a1 1 0 0 1 1-1h3.5a1 1 0 0 1 1 1c0 1.25.2 2.45.57 3.57a1 1 0 0 1-.25 1z"/>
        </svg>
        0431 286 517
      </p>
      <p class="contact__line">
        <svg class="contact__icon" viewBox="0 0 24 24" aria-hidden="true">
          <rect x="2" y="5" width="20" height="14" rx="1" fill="#17a3e6"/>
          <path d="M2.5 6l9.5 7 9.5-7" fill="none" stroke="#ffffff" stroke-width="1.6"/>
        </svg>
        rowan@tbk-plumbing.com.au
      </p>
    </div>

    <p class="abn"><span class="abn__label">Company ABN</span> - 73 215 904 386</p>
  </section>
</body>
</html>
```